Flag Order

We were just looking to order some branding flags to put on our rental equipment for our business. We would like different examples of the colors, shapes, sizes, backgrounds etc. Was thinking of just doing the plains icon instead of the whole logo on there. but open to ideas. preferably not a white background as they could get dirty,

```html
<!DOCTYPE html>
<html lang="en">
<head>
<meta charset="utf-8">
<title>Branding Flag – Pushing You Further</title>
<link href="https://fonts.googleapis.com/css2?family=Manrope:wght@700&display=swap" rel="stylesheet">
<style>
  :root {
    --stage: #4d4d4d;
    --flag: #2b2b2b;
    --ink: #ffffff;
    --accent: #1a8fe3;
  }
  html, body {
    margin: 0;
    padding: 0;
    width: 1200px;
    height: 1200px;
    overflow: hidden;
    background: var(--stage);
  }
  .canvas {
    position: relative;
    width: 1200px;
    height: 1200px;
    background: var(--stage);
  }
  .flag {
    position: absolute;
    left: 400px;
    top: 34px;
    width: 400px;
    height: 1132px;
    background: var(--flag);
    font-family: "Manrope", sans-serif;
    color: var(--ink);
  }
  .flag__slogan {
    position: absolute;
    left: 64px;
    top: 428px;
    margin: 0;
    font-size: 70px;
    font-weight: 700;
    line-height: 78px;
    letter-spacing: -0.5px;
  }
  .flag__brand {
    position: absolute;
    right: 28px;
    bottom: 78px;
    display: flex;
    align-items: center;
    gap: 14px;
  }
  .flag__brand-square {
    width: 34px;
    height: 34px;
    background: var(--accent);
  }
  .flag__brand-name {
    font-size: 44px;
    font-weight: 700;
    line-height: 1;
    color: var(--ink);
  }
</style>
</head>
<body>
  <main class="canvas">
    <section class="flag">
      <h1 class="flag__slogan">Pushing<br>You<br>Further</h1>
      <div class="flag__brand">
        <span class="flag__brand-square"></span>
        <span class="flag__brand-name">Northway</span>
      </div>
    </section>
  </main>
</body>
</html>
```